VTMB site redesign

Please redesign a home page with content provided. PSD only - no coding
Can use any images from Snapwelder.com

Please create a site design that more clearly illustrates the client's services and expertise. We are looking for a high-end design.

Any images used must be generic or of Dallas TX.

Fonts: Any
Colors: Match to logo
Look: Modern - Professional

Target Market(s)

medium-large business owners

Number of Pages Required

1 page

Font styles to use
Serif
Sans Serif

Requirements
Must have
• cohesive professional design
• high end look
• Match to logo

```html
<!DOCTYPE html>
<html lang="en">
<head>
<meta charset="utf-8">
<title>VTMB – Valemont Trade Market Brokers</title>
<link rel="stylesheet" href="https://fonts.googleapis.com/css2?family=Lato:wght@400;700;900&family=Poppins:wght@300;400;500&family=PT+Serif:wght@400;700&display=swap">
<style>
:root{
  --red:#c8101e;
  --red-soft:#d34348;
  --ink:#111;
  --grey:#8a8a8a;
  --light:#f4f4f4;
  --black:#050505;
  --white:#fff;
  --serif:"PT Serif", Georgia, serif;
  --sans:"Poppins", Arial, sans-serif;
  --display:"Lato", Arial, sans-serif;
}
*{box-sizing:border-box;margin:0;padding:0}
html,body{width:1200px;height:3297px;overflow:hidden}
body{font-family:var(--sans);color:var(--ink);background:var(--white);position:relative}
.abs{position:absolute}

/* top bar */
.topbar{position:absolute;top:0;left:0;width:1200px;height:48px;background:var(--red);color:var(--white);display:flex;align-items:center;justify-content:space-between;padding:0 77px}
.topbar .phone{display:flex;align-items:center;gap:10px;font-family:var(--display);font-weight:700;font-size:19px}
.topbar .social{display:flex;gap:16px}
.topbar .social span{width:14px;height:14px;border-radius:50%;background:rgba(255,255,255,.85)}

/* nav */
.nav{position:absolute;top:48px;left:0;width:1200px;height:106px;display:flex;align-items:center;justify-content:space-between;padding:0 77px}
.brand{display:flex;align-items:center;gap:12px}
.brand .mark{width:30px;height:30px;background:var(--red)}
.brand .name{font-family:var(--serif);font-weight:700;font-size:38px;color:var(--red);letter-spacing:2px}
.nav ul{list-style:none;display:flex;gap:44px;font-size:15px;color:#444}
.nav li.active{color:var(--red)}

/* hero */
.hero{position:absolute;top:154px;left:0;width:1200px;height:576px;background:linear-gradient(180deg,#56606a 0%,#3b4650 45%,#2f3b2e 80%,#1f2a1a 100%);text-align:center;color:var(--white)}
.hero h1{position:absolute;top:150px;width:100%;font-family:var(--display);font-weight:900;font-size:84px;line-height:1}
.hero h2{position:absolute;top:255px;width:100%;font-family:var(--display);font-weight:700;font-size:33px}
.hero p{position:absolute;top:300px;width:100%;font-family:var(--display);font-weight:700;font-size:21px}
.btn-red{position:absolute;top:362px;left:435px;width:330px;height:50px;background:var(--red);border:2px solid #e86a70;color:var(--white);font-family:var(--display);font-size:23px;display:flex;align-items:center;justify-content:center}

/* section headings */
.sec-title{position:absolute;width:100%;text-align:center;font-family:var(--serif);color:var(--red);font-size:46px;font-weight:400;letter-spacing:1px}
.lead{position:absolute;left:150px;width:900px;text-align:center;font-size:14px;line-height:24px;color:var(--grey);font-weight:300}

/* about */
.about{position:absolute;top:730px;left:0;width:1200px;height:549px}
.features{position:absolute;top:240px;left:77px;width:1046px;display:grid;grid-template-columns:repeat(4,1fr);text-align:center}
.feature .icon{width:108px;height:108px;margin:0 auto;border-radius:50%;background:radial-gradient(circle at 40% 35%,#e4404a,#b40d18);box-shadow:0 6px 10px rgba(0,0,0,.25);border:4px solid #eee;display:flex;align-items:center;justify-content:center}
.feature h3{font-family:var(--serif);font-weight:400;font-size:22px;margin-top:34px}
.feature p{font-size:13.5px;line-height:22px;color:var(--grey);width:205px;margin:8px auto 0;font-weight:300}

/* band */
.band{position:absolute;top:1279px;left:0;width:1200px;height:183px;background:var(--red-soft);color:rgba(255,255,255,.75);font-family:var(--serif);font-size:29px;line-height:42px}
.band p{position:absolute;top:48px;left:80px;width:800px}
.band b{color:var(--white);font-weight:700}
.band .calc{position:absolute;top:66px;left:895px;width:226px;height:48px;background:var(--white);color:var(--red);font-family:var(--sans);font-size:20px;display:flex;align-items:center;justify-content:center;box-shadow:3px 3px 0 rgba(0,0,0,.25)}

/* team */
.team{position:absolute;top:1462px;left:0;width:1200px;height:659px}
.members{position:absolute;top:215px;left:244px;display:flex;gap:77px}
.member{width:187px}
.member .photo{width:187px;height:187px;background:linear-gradient(180deg,#ededed 0%,#d9d9d9 55%,#2a2e35 100%)}
.member h4{font-family:var(--serif);font-weight:400;color:var(--red);font-size:21px;margin-top:18px;white-space:nowrap}
.member p{font-size:13.5px;line-height:20px;color:var(--grey);margin-top:8px;font-weight:300}
.member .more{font-size:14px;color:var(--ink);margin-top:18px;font-weight:500}

/* testimonial */
.testimonial{position:absolute;top:2121px;left:0;width:1200px;height:359px;background:var(--black);color:var(--white)}
.testimonial blockquote{position:absolute;top:143px;left:165px;width:870px;text-align:center;font-size:14px;line-height:24px;color:#cfcfcf;font-weight:300}
.testimonial cite{position:absolute;top:248px;width:100%;text-align:center;font-family:var(--serif);font-style:normal;font-size:17px}
.testimonial .rule{position:absolute;top:286px;left:150px;width:900px;height:1px;background:linear-gradient(90deg,transparent,#666,transparent)}
.testimonial .pointer{position:absolute;top:279px;left:593px;width:0;height:0;border-left:7px solid transparent;border-right:7px solid transparent;border-bottom:7px solid var(--white)}

/* news */
.news{position:absolute;top:2480px;left:0;width:1200px;height:443px}
.cards{position:absolute;top:131px;left:77px;display:flex;gap:20px}
.card{width:336px;height:246px;background:var(--light)}
.card .img{height:143px;border-bottom:3px solid #222}
.card h5{font-family:var(--serif);font-weight:400;color:var(--red);font-size:17px;line-height:26px;padding:20px 30px 0}

/* footer */
.footer{position:absolute;top:2923px;left:0;width:1200px;height:374px;background:var(--red);color:var(--white)}
.footer h6{position:absolute;top:52px;font-size:15px;font-weight:400;letter-spacing:.5px}
.form{position:absolute;top:93px;left:77px;width:495px;display:grid;grid-template-columns:1fr 1fr;gap:6px}
.form span{height:42px;background:var(--white);color:#bbb;font-size:12px;padding:0 12px;display:flex;align-items:center}
.form .msg{grid-column:1/3;height:42px}
.send{position:absolute;top:238px;left:77px;width:154px;height:48px;background:var(--white);color:var(--red);font-size:20px;display:flex;align-items:center;justify-content:center;box-shadow:3px 3px 0 rgba(0,0,0,.25)}
.contact{position:absolute;top:92px;left:609px;font-size:14px;line-height:21px}
.contact li{list-style:none;display:flex;gap:14px;margin-bottom:22px;align-items:flex-start}
.contact svg{flex:none;margin-top:2px}
.f-brand{position:absolute;top:66px;left:898px;width:196px;height:104px;background:var(--white);display:flex;align-items:center;justify-content:center;gap:10px}
.f-brand .mark{width:22px;height:22px;background:var(--red)}
.f-brand .name{font-family:var(--serif);font-weight:700;font-size:34px;color:var(--red);letter-spacing:2px}
.f-social{position:absolute;top:190px;left:885px;display:flex;gap:13px}
.f-social span{width:46px;height:46px;border-radius:50%;border:2px solid rgba(255,255,255,.7)}
.f-social span:first-child{background:var(--white);border-color:var(--white)}
.footer .divider{position:absolute;top:318px;left:77px;width:1046px;height:1px;background:rgba(255,255,255,.5)}
.footer .copy{position:absolute;top:335px;width:100%;text-align:center;font-size:13px;color:rgba(255,255,255,.85)}
</style>
</head>
<body>

<div class="topbar">
  <div class="phone">
    <svg width="16" height="16" viewBox="0 0 24 24" fill="#fff"><path d="M6.6 10.8a15 15 0 0 0 6.6 6.6l2.2-2.2c.3-.3.7-.4 1-.2 1.1.4 2.3.6 3.6.6.6 0 1 .4 1 1V20c0 .6-.4 1-1 1A17 17 0 0 1 3 4c0-.6.4-1 1-1h3.5c.6 0 1 .4 1 1 0 1.3.2 2.5.6 3.6.1.3 0 .7-.2 1z"/></svg>
    214-555-0126
  </div>
  <div class="social"><span></span><span></span><span></span><span></span></div>
</div>

<header class="nav">
  <div class="brand"><span class="mark"></span><span class="name">VTMB</span></div>
  <ul>
    <li class="active">Home</li><li>About VTMB</li><li>Services</li><li>Blog</li><li>Market News</li><li>Contact Us</li>
  </ul>
</header>

<section class="hero" role="img" aria-label="Dallas skyline photograph above a line of green trees">
  <h1>VTMB</h1>
  <h2>The Best Commercial Tenant Reps in Dallas TX!</h2>
  <p>Let us Handle Your Commercial Real Estste Lease Negotiations!</p>
  <div class="btn-red">CAll VTMB at 214 - 555- 0141!</div>
</section>

<section class="about">
  <h2 class="sec-title" style="top:52px">ABOUT US</h2>
  <p class="lead" style="top:127px">Valemont Trade Market Brokers, a division of The Valemont Companies, was founded in 1982. An authority in the field of leasing and sales of office and industrial space in the Dallas Fort Worth area of Texas, VTMB specializes in the area of commercial real estate by acting as tenant representatives in Dallas and Fort Worth Texas to help our clients find the best Dallas commercial office space to meet their needs.</p>
  <div class="features">
    <div class="feature">
      <div class="icon"><svg width="50" height="50" viewBox="0 0 50 50" fill="none" stroke="#fff" stroke-width="2.5" stroke-linejoin="round"><path d="M20 6h10l-2 6h-6z"/><path d="M22 12l-5 24 8 8 8-8-5-24"/></svg></div>
      <h3>Relationships</h3>
      <p>Save time by trusting VTMB year after year to find the right location for you. Once we've worked together,...</p>
    </div>
    <div class="feature">
      <div class="icon"><svg width="52" height="50" viewBox="0 0 52 50" fill="none" stroke="#fff" stroke-width="2.5" stroke-linejoin="round"><path d="M6 24L26 6l20 18"/><path d="M11 20v24h30V20"/><path d="M21 44V31h10v13"/></svg></div>
      <h3>Access to More</h3>
      <p>We have no agreements or personal incentives for specific properties, so we can always show you...</p>
    </div>
    <div class="feature">
      <div class="icon"><svg width="50" height="50" viewBox="0 0 50 50" fill="none" stroke="#fff" stroke-width="2.5" stroke-linejoin="round"><path d="M15 6h20v12a10 10 0 0 1-20 0z"/><path d="M15 10H8c0 7 3 10 8 11M35 10h7c0 7-3 10-8 11"/><path d="M25 28v8M17 44h16l-2-8H19z"/></svg></div>
      <h3>Free To You</h3>
      <p>You pay us nothing. We get our commission from the property being leased...</p>
    </div>
    <div class="feature">
      <div class="icon"><svg width="50" height="50" viewBox="0 0 50 50" fill="none" stroke="#fff" stroke-width="2.5"><circle cx="25" cy="25" r="18"/><ellipse cx="25" cy="25" rx="8" ry="18"/><path d="M7 25h36M10 16h30M10 34h30"/></svg></div>
      <h3>Customized Service</h3>
      <p>Aside from saving you the time of repeating what your needs are to each new location...</p>
    </div>
  </div>
</section>

<section class="band">
  <p>If you need to find office or warehouse space in the <b>Dallas Fort Worth area,</b> the team at VTMB has the experience you need.</p>
  <div class="calc">Space Calculator</div>
</section>

<section class="team">
  <h2 class="sec-title" style="top:60px">OUR TEAM</h2>
  <p class="lead" style="top:138px">Our team members are among the best commercial real estate brokers and agents in Dallas and Fort Worth; we are committed to your success and want to help you fulfill your commercial real estate needs. The highly qualified and experienced professionals at VTMB are ready to serve your needs today!</p>
  <div class="members">
    <div class="member">
      <div class="photo" role="img" aria-label="Portrait photo of a team member in a dark suit"></div>
      <h4>Warren H. Valemont</h4>
      <p>Warren Valemont, a licensed Texas Real Estate Broker, founded The Valemont Companies, VTMB...</p>
      <div class="more">READ MORE »</div>
    </div>
    <div class="member">
      <div class="photo" role="img" aria-label="Portrait photo of a team member in a dark suit"></div>
      <h4>Colin Reyes-Hart</h4>
      <p>Colin Reyes-Hart has been with VTMB since 1990 and serves as the Senior Director. Colin is a licensed Texas...</p>
      <div class="more">READ MORE »</div>
    </div>
    <div class="member">
      <div class="photo" role="img" aria-label="Portrait photo of a team member in a dark suit"></div>
      <h4>Daniel Joseph Keller</h4>
      <p>Daniel has been with VTMB since 2016. Focused on tenant representation, his responsibilities...</p>
      <div class="more">READ MORE »</div>
    </div>
  </div>
</section>

<section class="testimonial">
  <h2 class="sec-title" style="top:60px">TESTIMONIAL</h2>
  <blockquote>"The real estate team at VTMB has decades of experience in Commercial. One advantage of VTMB is they know all the properties that are about to become available, BEFORE they are available. They have the inside track on properties and they watch your back at the negotiating table. Very impressive with a polished approach. Let the team run with your next project and you won't be disappointed."</blockquote>
  <cite>- Andrew Thomas Whitfield</cite>
  <div class="rule"></div>
  <div class="pointer"></div>
</section>

<section class="news">
  <h2 class="sec-title" style="top:58px">LATEST NEWS</h2>
  <div class="cards">
    <article class="card">
      <div class="img" role="img" aria-label="Photo of a businessman in a suit with a city backdrop" style="background:linear-gradient(135deg,#c9ccd2,#5b6c85 55%,#1e2838)"></div>
      <h5>6 Important Key Aspects of Tenant Representation To Know!</h5>
    </article>
    <article class="card">
      <div class="img" role="img" aria-label="Photo of a bright open-plan office interior" style="background:linear-gradient(135deg,#f1e6d6,#c9a47a 55%,#6b4c34)"></div>
      <h5>How Does Landlord Recapture Relate To My Office Lease?</h5>
    </article>
    <article class="card">
      <div class="img" role="img" aria-label="Photo of office towers against a blue sky" style="background:linear-gradient(160deg,#7fa6d6,#3c69a8 50%,#2a3340)"></div>
      <h5>Do You Need Office Space? Don't Miss These Flexible Options!</h5>
    </article>
  </div>
</section>

<footer class="footer">
  <h6 style="left:80px">WE LOOK FORWARD TO HEARING FROM YOU.</h6>
  <div class="form">
    <span>Name</span><span>Company Info</span>
    <span>Phone</span><span>E-Mail</span>
    <span class="msg">Message</span>
  </div>
  <div class="send">Send</div>

  <h6 style="left:609px">CONTACT INFO</h6>
  <ul class="contact">
    <li><svg width="20" height="18" viewBox="0 0 20 18" fill="none" stroke="#fff" stroke-width="1.5"><path d="M1 3l6-2 6 2 6-2v14l-6 2-6-2-6 2z"/><path d="M7 1v14M13 3v14"/></svg><span>1450 Cedar Grove Avenue<br>@ Linden, Suite 850<br>Dallas, Texas 75219</span></li>
    <li><svg width="18" height="18" viewBox="0 0 24 24" fill="none" stroke="#fff" stroke-width="1.8"><path d="M6.6 10.8a15 15 0 0 0 6.6 6.6l2.2-2.2c.3-.3.7-.4 1-.2 1.1.4 2.3.6 3.6.6.6 0 1 .4 1 1V20c0 .6-.4 1-1 1A17 17 0 0 1 3 4c0-.6.4-1 1-1h3.5c.6 0 1 .4 1 1 0 1.3.2 2.5.6 3.6.1.3 0 .7-.2 1z"/></svg><span>214-555-0147</span></li>
    <li><svg width="18" height="18" viewBox="0 0 20 20" fill="none" stroke="#fff" stroke-width="1.5"><rect x="2" y="7" width="16" height="10"/><path d="M5 7V2h10v5M5 13h10"/></svg><span>214-555-0147</span></li>
  </ul>

  <div class="f-brand"><span class="mark"></span><span class="name">VTMB</span></div>
  <div class="f-social"><span></span><span></span><span></span><span></span></div>

  <div class="divider"></div>
  <div class="copy">© VTMB Valemont Trade Market Brokers - 2018. All Rights Reserved.</div>
</footer>

</body>
</html>
```